Business Card - connecting 2 souls and beggining the journey of self discovery

Logo on the front
with tag line

On the back list of services and contact details

Seminars
workshops
Coaching
podcasts

Darren Whitlow
Health & Wellbeing Life Coach
0491 372 615
darren@brightcoreliving.example
brightcoreliving.example

Industry/Entity Type

Life Coaching

Contact Information for Business Card

I like the use of colour from the logo to be used. I'm not a fan of white.

Requirements
Must have
• My tagline: The journey home starts with you
Nice to have
• Use of colour that is in the Brightcore Living logo

```html
<!DOCTYPE html>
<html lang="en">
<head>
<meta charset="utf-8">
<title>Darren Whitlow – Business Card</title>
<link href="https://fonts.googleapis.com/css2?family=Open+Sans:wght@400;600&family=Montserrat:wght@500&display=swap" rel="stylesheet">
<style>
  :root {
    --stage: #e9e7e4;
    --card: #1f2a33;
    --mint: #7fe3a3;
    --white: #f4f6f7;
    --silver: #c8cdd1;
    --brand-dot: #f5a66b;
    --dot-a: #b98cf7;
    --dot-b: #f7d86a;
    --dot-c: #5fe0c4;
    --dot-d: #f59ac0;
  }
  * { margin: 0; padding: 0; box-sizing: border-box; }
  html, body { width: 1200px; height: 900px; overflow: hidden; background: var(--stage); }
  body { position: relative; font-family: "Open Sans", sans-serif; color: var(--white); }

  .card {
    position: absolute;
    background: var(--card);
    box-shadow: 0 10px 28px rgba(0,0,0,0.22);
  }
  .card-front { left: 238px; top: 62px; width: 555px; height: 343px; }
  .card-back  { left: 457px; top: 518px; width: 560px; height: 344px; }

  /* brand block */
  .brand { position: absolute; display: flex; align-items: center; }
  .brand-dot { border-radius: 50%; background: var(--brand-dot); flex: none; }
  .brand-name { font-weight: 600; color: var(--white); line-height: 1.15; }

  .card-front .brand { left: 62px; top: 110px; gap: 14px; }
  .card-front .brand-dot { width: 62px; height: 62px; }
  .card-front .brand-name { font-size: 22px; }

  .holder { position: absolute; left: 289px; top: 74px; }
  .holder-name { font-size: 19px; font-weight: 600; color: var(--mint); letter-spacing: 0.3px; text-transform: uppercase; line-height: 1.1; }
  .holder-role { font-size: 14.5px; color: var(--white); margin-top: 1px; }

  .contact { position: absolute; left: 292px; top: 158px; list-style: none; font-size: 14.5px; }
  .contact li { display: flex; align-items: center; gap: 5px; height: 20.5px; }
  .contact svg { width: 10px; height: 10px; fill: var(--mint); flex: none; }

  .services { position: absolute; left: 78px; top: 276px; display: flex; gap: 11px; list-style: none; font-size: 14px; letter-spacing: 0.2px; }
  .services li { display: flex; align-items: center; gap: 6px; }
  .services li::before { content: ""; width: 9px; height: 9px; border-radius: 50%; background: var(--dot); }
  .services li:nth-child(1) { --dot: var(--dot-a); }
  .services li:nth-child(2) { --dot: var(--dot-b); }
  .services li:nth-child(3) { --dot: var(--dot-c); }
  .services li:nth-child(4) { --dot: var(--dot-d); }

  .card-back .brand { left: 0; right: 0; top: 86px; flex-direction: column; gap: 8px; }
  .card-back .brand-dot { width: 84px; height: 84px; }
  .card-back .brand-name { font-size: 17px; }

  .tagline {
    position: absolute; left: 0; right: 0; top: 222px; text-align: center;
    font-family: "Montserrat", sans-serif; font-weight: 500; font-size: 27px;
    color: var(--silver); letter-spacing: -0.5px;
    text-shadow: 0 2px 4px rgba(0,0,0,0.6);
  }
</style>
</head>
<body>

<section class="card card-front">
  <div class="brand">
    <span class="brand-dot"></span>
    <span class="brand-name">Brightcore<br>Living</span>
  </div>

  <div class="holder">
    <p class="holder-name">Darren Whitlow</p>
    <p class="holder-role">Health &amp; Wellbeing Life Coach</p>
  </div>

  <ul class="contact">
    <li>
      <svg viewBox="0 0 10 10" aria-hidden="true"><path d="M2 0.5 3.6 2.8 2.7 3.8C3.3 5 4.9 6.7 6.2 7.3L7.2 6.4 9.5 8 8.6 9.5C5 9.5 0.5 5 0.5 1.4Z"/></svg>
      0491 372 615
    </li>
    <li>
      <svg viewBox="0 0 10 10" aria-hidden="true"><path d="M0.5 2h9v6.5h-9z M0.9 2.4 5 5.6 9.1 2.4" stroke="#1f2a33" stroke-width="0.8"/></svg>
      darren@brightcoreliving.example
    </li>
    <li>
      <svg viewBox="0 0 10 10" aria-hidden="true"><circle cx="5" cy="5" r="4.6"/></svg>
      www.brightcoreliving.example
    </li>
  </ul>

  <ul class="services">
    <li>SEMINARS</li>
    <li>WORKSHOPS</li>
    <li>COACHING</li>
    <li>PODCASTS</li>
  </ul>
</section>

<section class="card card-back">
  <div class="brand">
    <span class="brand-dot"></span>
    <span class="brand-name">Brightcore Living</span>
  </div>
  <p class="tagline">The journey home starts with you</p>
</section>

</body>
</html>
```